New Webpage for High Class Expert Witness Services Company

We are looking for a minimalist design for a webpage that just has our logo and an entry form offer to connect with one of our Liaisons.
The entry form should just ask for Name, Email, Contact Info and Description of Project.

Company Name is: The Marlowe Crest Advisory Services

Number of Pages Required

1 page

```html
<!DOCTYPE html>
<html lang="en">
<head>
<meta charset="UTF-8">
<title>Marlowe Crest Advisory Services</title>
<link rel="stylesheet" href="https://fonts.googleapis.com/css2?family=Cinzel:wght@400;700&family=Manrope:wght@400&family=Roboto:wght@400&display=swap">
<style>
  :root {
    --bg: #0b0b0b;
    --mesh-mid: #2a2a2a;
    --mesh-light: #3a3a3a;
    --text-light: #ececec;
    --text-muted: #8e8e8e;
    --body-text: #d4d4d4;
    --rule: #555555;
    --panel-top: #e2e3e5;
    --panel-bottom: #b5b6ba;
    --field: #ffffff;
    --ink: #111111;
    --button: #000000;
    --footer-bg: #000000;
    --footer-text: #a8a8a8;
  }
  * { margin: 0; padding: 0; box-sizing: border-box; }
  html, body { width: 1200px; height: 740px; overflow: hidden; background: var(--bg); }
  .page { position: relative; width: 1200px; height: 740px; background: var(--bg); font-family: "Manrope", sans-serif; }

  .mesh-backdrop {
    position: absolute; left: 0; top: 420px; width: 1200px; height: 259px;
    background:
      radial-gradient(ellipse 60% 70% at 50% 90%, var(--mesh-light) 0%, transparent 70%),
      linear-gradient(180deg, transparent 0%, var(--mesh-mid) 55%, #1c1c1c 100%);
    opacity: 0.85;
  }

  .brand-name {
    position: absolute; left: 115px; top: 52px;
    font-family: "Cinzel", serif; font-weight: 400; font-size: 28px; line-height: 32px;
    color: var(--text-light); letter-spacing: 1px;
    display: flex; align-items: center; gap: 12px;
  }
  .brand-mark { width: 22px; height: 22px; background: var(--text-light); }
  .brand-name .tagline { display: block; font-size: 10px; line-height: 14px; letter-spacing: 2.6px; color: var(--text-muted); }

  .hero { position: absolute; left: 116px; top: 231px; border-left: 1px solid var(--rule); padding-left: 12px; height: 123px; }
  .hero-eyebrow { font-family: "Cinzel", serif; font-size: 19px; letter-spacing: 2.4px; color: var(--text-muted); line-height: 24px; margin-top: -6px; }
  .hero-title {
    font-family: "Cinzel", serif; font-weight: 400; font-size: 46px; line-height: 51px; margin-top: 12px;
    background: linear-gradient(90deg, #f2f2f2 0%, #f2f2f2 60%, #9a9a9a 100%);
    -webkit-background-clip: text; background-clip: text; color: transparent;
  }
  .hero-copy { position: absolute; left: 115px; top: 372px; width: 500px; font-size: 14.5px; line-height: 28px; color: var(--body-text); }

  .contact-panel {
    position: absolute; left: 716px; top: 123px; width: 377px; height: 437px;
    background: linear-gradient(170deg, var(--panel-top) 0%, var(--panel-bottom) 100%);
    border: 1px solid #9c9c9c;
  }
  .contact-title { position: absolute; left: 45px; top: 36px; font-family: "Cinzel", serif; font-size: 27px; color: var(--ink); letter-spacing: 0.3px; }
  .field {
    position: absolute; left: 44px; width: 295px; height: 42px; background: var(--field); border: none;
    font-family: "Roboto", sans-serif; font-size: 13px; color: var(--ink); padding: 0 18px;
  }
  .field::placeholder { color: var(--ink); }
  .field-name { top: 85px; }
  .field-email { top: 143px; }
  .field-phone { top: 197px; }
  .field-description { top: 253px; height: 89px; padding-top: 12px; resize: none; }
  .submit-button {
    position: absolute; left: 43px; top: 354px; width: 297px; height: 44px;
    background: var(--button); color: #ffffff; border: none;
    font-family: "Cinzel", serif; font-weight: 700; font-size: 15px; letter-spacing: 0.5px;
  }

  .site-footer {
    position: absolute; left: 0; top: 679px; width: 1200px; height: 61px; background: var(--footer-bg);
    font-family: "Roboto", sans-serif; font-size: 12.5px; color: var(--footer-text);
    display: flex; align-items: center; justify-content: center;
  }
</style>
</head>
<body>
<div class="page">
  <div class="mesh-backdrop" role="img" aria-label="Soft grey hexagonal mesh wave backdrop"></div>

  <div class="brand-name">
    <span class="brand-mark"></span>
    <span>Marlowe Crest<span class="tagline">Advisory Services</span></span>
  </div>

  <div class="hero">
    <p class="hero-eyebrow">MARLOWE CREST ADVISORY SERVICES</p>
    <h1 class="hero-title">SEAMLESS MEDICAL<br>EXPERT INTEGRATION</h1>
  </div>
  <p class="hero-copy">Lorem ipsum dolor sit amet, consectetur adipiscing elit, sed do eiusmod tempor incididunt ut labore et dolore magna aliqua.</p>

  <form class="contact-panel">
    <h2 class="contact-title">CONNECT WITH US</h2>
    <input class="field field-name" type="text" placeholder="Name*">
    <input class="field field-email" type="email" placeholder="Email*">
    <input class="field field-phone" type="tel" placeholder="Phone number*">
    <textarea class="field field-description" placeholder="Description of Project"></textarea>
    <button class="submit-button" type="submit">SUBMIT</button>
  </form>

  <footer class="site-footer">© 2026 Marlowe Crest Advisory Services. All Rights Reserved</footer>
</div>
</body>
</html>
```